Design of Postcards for pairova.ch - to promote this online dating platform

Tobias and me, we operate a dating platform called
pairova.ch.

pairova.ch

On this platform you find members with whom you can spend your spare time, share your hobbies or find a partner or a friend.

we need 5 different postcard designs; means, we will send the postcards to our members; they will send the postcards to their friends and colleagues in order to find and win new members for our platform.

we are looking forward receiving your draft designs. for postcards in the format DIN A6 (mm 105 × 148). these postcards should promote and communicate our brand, our colors, our url, pairova.ch, and the topic of finding a friend, a colleague, a partner, someone to spend your time or life with.

thnx, Tobias 6 Reto

Target Market(s)

adults age 30-45

Industry/Entity Type

Dating

Font styles to use
Decorative
Script

Requirements
Must have
• please find logo of pairova.ch on our website, pairova.ch
• if possible using colors of pairova.ch, please see website
• postcards should appeal men and women.

```html
<!DOCTYPE html>
<html lang="en">
<head>
<meta charset="utf-8">
<title>pairova.ch – Postcard</title>
<link rel="stylesheet" href="https://fonts.googleapis.com/css2?family=Sacramento&family=Ubuntu:wght@400;700&display=swap">
<style>
  :root {
    --brand-crimson: #8c1c48;
    --brand-plum: #5a1f3b;
    --tint-blush: #f3e5ea;
    --tint-blush-deep: #ead2da;
    --photo-warm: #d9b6a4;
    --photo-cool: #b9a8a6;
    --text-grey: #6b6166;
    --card-white: #ffffff;
    --stage: #2b2b2b;
  }
  html, body {
    margin: 0;
    width: 1200px;
    height: 960px;
    overflow: hidden;
    background: var(--stage);
  }
  .postcard {
    position: absolute;
    left: 50px;
    top: 90px;
    width: 1100px;
    height: 780px;
    background: var(--card-white);
    overflow: hidden;
  }
  .postcard__art {
    position: absolute;
    inset: 0;
  }
  .brand {
    position: absolute;
    right: 72px;
    top: 44px;
    text-align: left;
  }
  .brand__row {
    display: flex;
    align-items: center;
    gap: 12px;
  }
  .brand__dot {
    width: 40px;
    height: 40px;
    border-radius: 50%;
    background: var(--brand-crimson);
  }
  .brand__name {
    font-family: "Ubuntu", sans-serif;
    font-weight: 700;
    font-size: 50px;
    line-height: 1;
    letter-spacing: 1px;
    text-transform: uppercase;
    color: var(--brand-crimson);
  }
  .brand__tagline {
    margin: 8px 0 0 52px;
    font-family: "Ubuntu", sans-serif;
    font-weight: 400;
    font-size: 17px;
    letter-spacing: 1.6px;
    text-transform: uppercase;
    color: var(--text-grey);
  }
  .message {
    position: absolute;
    right: 72px;
    top: 176px;
    margin: 0;
    text-align: right;
    font-family: "Sacramento", cursive;
    font-weight: 400;
    font-size: 58px;
    line-height: 79px;
    color: var(--brand-plum);
  }
  .web-address {
    position: absolute;
    right: 72px;
    top: 700px;
    margin: 0;
    font-family: "Ubuntu", sans-serif;
    font-size: 29px;
    color: var(--brand-plum);
  }
</style>
</head>
<body>
  <main class="postcard">
    <svg class="postcard__art" width="1100" height="780" viewBox="0 0 1100 780">
      <defs>
        <linearGradient id="photo-tone" x1="0" y1="0" x2="1" y2="1">
          <stop offset="0" stop-color="#f6eeea"/>
          <stop offset="0.45" stop-color="var(--photo-warm)"/>
          <stop offset="1" stop-color="var(--photo-cool)"/>
        </linearGradient>
        <linearGradient id="faint-tone" x1="0" y1="0" x2="1" y2="1">
          <stop offset="0" stop-color="var(--tint-blush)"/>
          <stop offset="1" stop-color="var(--tint-blush-deep)"/>
        </linearGradient>
      </defs>

      <path class="backdrop-bubble backdrop-bubble--left" role="img"
            aria-label="Faded photo of a laughing couple in a pale speech bubble"
            d="M0 0 H560 Q610 90 520 200 L0 420 Z" fill="url(#faint-tone)" opacity="0.75"/>

      <path class="backdrop-bubble backdrop-bubble--right" role="img"
            aria-label="Faded photo of a smiling couple in a large pale speech bubble"
            d="M1010 560 L1055 770 L920 640 A275 275 0 1 1 1010 560 Z"
            fill="url(#faint-tone)" opacity="0.85"/>

      <path class="hero-bubble" role="img"
            aria-label="Photo of a happy couple making a heart shape with their hands"
            d="M616 591 L681 736 L446 699 A334 334 0 1 1 616 591 Z"
            fill="url(#photo-tone)" stroke="var(--brand-crimson)" stroke-width="4" stroke-linejoin="round"/>
    </svg>

    <header class="brand">
      <div class="brand__row">
        <span class="brand__dot"></span>
        <span class="brand__name">pairova.ch</span>
      </div>
      <div class="brand__tagline">Die Partnersuche der Schweiz</div>
    </header>

    <p class="message">
      find members<br>
      with whom you can<br>
      spend your spare time,<br>
      share your hobbies<br>
      or find a partner<br>
      or a friend.
    </p>

    <p class="web-address">www.pairova.ch</p>
  </main>
</body>
</html>
```